Structural Engineering Business Card

Brookvane Drafting does residential house plans for clients in Central Florida. Would like simple but elegant business card that is appropriate for a house plan engineering company. Prefer black business card with black/white them but open to other shades of blue. I uploaded a sample card that I came across that looked good but please come up with your own creative designs.

Contact Information for Business Card

Name, Title, Phone, Email, Address, website

```html
<!DOCTYPE html>
<html lang="en">
<head>
<meta charset="utf-8">
<title>Brookvane Drafting – Business Card</title>
<link rel="stylesheet" href="https://fonts.googleapis.com/css2?family=Montserrat:wght@400;600;700&display=swap">
<style>
  :root {
    --backdrop: #1d1d1e;
    --card: #2b2b2c;
    --card-edge: #4cb5d8;
    --accent: #4fb9dc;
    --text: #e9e9e9;
    --muted: #9a9a9a;
    --drawing-a: #3a3b3d;
    --drawing-b: #2f3031;
  }
  * { box-sizing: border-box; margin: 0; padding: 0; }
  html, body { width: 1200px; height: 900px; overflow: hidden; }
  body {
    background: var(--backdrop);
    font-family: "Montserrat", sans-serif;
    position: relative;
  }
  .card {
    position: absolute;
    top: 100px;
    width: 400px;
    height: 700px;
    background: var(--card);
    border-radius: 26px;
    border-bottom: 4px solid var(--card-edge);
    border-left: 3px solid var(--card-edge);
    overflow: hidden;
  }
  .card--front { left: 170px; }
  .card--back { left: 630px; }

  .brand {
    display: flex;
    align-items: center;
    justify-content: center;
    gap: 12px;
  }
  .brand__mark {
    width: 22px; height: 22px;
    background: var(--accent);
    border-radius: 3px;
  }
  .brand__name {
    font-weight: 700;
    font-size: 30px;
    color: var(--muted);
    letter-spacing: 0.5px;
  }
  .card--front .brand { position: absolute; top: 150px; left: 0; right: 0; }
  .card--back .brand { position: absolute; bottom: 110px; left: 0; right: 0; }

  .person { position: absolute; top: 380px; left: 0; right: 0; text-align: center; }
  .person__name { font-weight: 700; font-size: 28px; color: var(--accent); }
  .person__title { font-size: 15px; color: var(--text); margin-top: 2px; }

  .icon-row {
    position: absolute; top: 475px; left: 40px; right: 40px;
    display: flex; align-items: center; gap: 10px;
  }
  .icon-row__rule { flex: 1; height: 2px; background: var(--accent); }
  .icon-row__icons { display: flex; gap: 6px; }
  .icon-tile {
    width: 30px; height: 30px; border-radius: 6px;
    background: var(--accent);
    display: flex; align-items: center; justify-content: center;
  }

  .contact {
    position: absolute; top: 522px; left: 0; right: 0;
    text-align: center; color: var(--text);
    font-size: 16px; line-height: 24px;
  }
  .divider {
    position: absolute; top: 610px; left: 50%;
    width: 70px; height: 2px; margin-left: -35px;
    background: var(--accent);
  }
  .address {
    position: absolute; top: 628px; left: 0; right: 0;
    text-align: center; color: var(--text);
    font-size: 16px; line-height: 22px;
  }

  .house-drawing {
    position: absolute; top: 50px; left: 30px;
    width: 340px; height: 420px;
    border-radius: 10px;
    background: linear-gradient(160deg, var(--drawing-a), var(--drawing-b));
  }
</style>
</head>
<body>

<section class="card card--front">
  <div class="brand">
    <span class="brand__mark"></span>
    <span class="brand__name">Brookvane Drafting</span>
  </div>

  <div class="person">
    <div class="person__name">Elena Marsh</div>
    <div class="person__title">Owner</div>
  </div>

  <div class="icon-row">
    <span class="icon-row__rule"></span>
    <div class="icon-row__icons">
      <span class="icon-tile" aria-label="Phone">
        <svg width="18" height="18" viewBox="0 0 24 24"><path d="M6.6 10.8a15 15 0 0 0 6.6 6.6l2.2-2.2a1 1 0 0 1 1-.25 11.4 11.4 0 0 0 3.6.57 1 1 0 0 1 1 1V20a1 1 0 0 1-1 1A17 17 0 0 1 3 4a1 1 0 0 1 1-1h3.5a1 1 0 0 1 1 1c0 1.25.2 2.45.57 3.57a1 1 0 0 1-.25 1z" fill="#2b2b2c"/></svg>
      </span>
      <span class="icon-tile" aria-label="Email">
        <svg width="18" height="18" viewBox="0 0 24 24"><rect x="3" y="6" width="18" height="12" rx="1" fill="#2b2b2c"/><path d="M3.5 6.5 12 13l8.5-6.5" stroke="#4fb9dc" stroke-width="1.6" fill="none"/></svg>
      </span>
      <span class="icon-tile" aria-label="Website">
        <svg width="18" height="18" viewBox="0 0 24 24" fill="none" stroke="#2b2b2c" stroke-width="2"><circle cx="12" cy="12" r="8.5"/><path d="M3.5 12h17M12 3.5c3 3 3 14 0 17M12 3.5c-3 3-3 14 0 17"/></svg>
      </span>
    </div>
    <span class="icon-row__rule"></span>
  </div>

  <div class="contact">
    <p>+1 407 555 0182</p>
    <p>info@brookvanedrafting.com</p>
    <p>www.brookvanedrafting.com</p>
  </div>

  <span class="divider"></span>

  <div class="address">
    <p>418 Palmetto Lane</p>
    <p>Orlando, FL 32801</p>
  </div>
</section>

<section class="card card--back">
  <div class="house-drawing" role="img" aria-label="Line-drawn elevation of a two-storey house with dimension lines"></div>
  <div class="brand">
    <span class="brand__mark"></span>
    <span class="brand__name">Brookvane Drafting</span>
  </div>
</section>

</body>
</html>
```